Easy Marinade Labels for Butchery Store

Need a set of labels designed for a Butchery Shop. They will sit in the top left corner of the packets as a triangle (7cm each side). Easy because the only major requirement is the label name and some small text saying "Please ask in store to see spec sheet for ingredients". Extra points for finding a fun way to incorporate the logo and/or images of food (garlic bulbs, chilli, spices ect) to enhance the label. List of Marinade Names below: GarlicPepper Mint & RosemarySatayBBQChilli Plum & GingerSundried Tomato & BasilBuffaloHoney SoyHoi-SinPer PeriSpicy CajunTeriyakiBlack Bean Ive also attached the logo and an example of how the label might sit on a packet of meat. Thanks

Target Market(s)

Butchery Deli Shop Customers

Industry/Entity Type

Food Store

Font styles to use
Serif
Sans Serif
Decorative
Other font styles liked:
• Fun font that isn't a generic Quellbrix Font?

Colors

Designer to choose colors to be used in the design.

Requirements
Must have
• Product Name
• Small text saying "Please ask in store to see spec sheet for ingredients"
Nice to have
• Photos of ingredients that would match that type of marinade - Chilli, Garlic, Spices.
• Fenly Oak Logo - not essential if it doesn't look good on the label / doesn't fit.

```html
<!DOCTYPE html>
<html lang="en">
<head>
<meta charset="utf-8">
<title>Sundried Tomato and Basil Marinade Label</title>
<link href="https://fonts.googleapis.com/css2?family=Amatic+SC:wght@700&family=Open+Sans:wght@800&display=swap" rel="stylesheet">
<style>
  :root {
    --paper: #ffffff;
    --frame-yellow: #f2e829;
    --tomato-red: #d9261c;
    --tomato-deep: #b81a16;
    --basil-green: #2f8a3a;
    --basil-deep: #1f5e2a;
    --label-ink: #ffffff;
  }
  html, body {
    margin: 0;
    padding: 0;
    width: 1200px;
    height: 900px;
    overflow: hidden;
    background: var(--paper);
  }
  .label-canvas {
    position: relative;
    width: 1200px;
    height: 900px;
  }
  .label-shape {
    position: absolute;
    inset: 0;
  }
  .marinade-name {
    font-family: "Amatic SC", "Comic Sans MS", cursive;
    font-weight: 700;
    fill: var(--label-ink);
  }
  .ingredients-note {
    font-family: "Open Sans", Arial, sans-serif;
    font-weight: 800;
    font-size: 20px;
    letter-spacing: 2.2px;
    fill: var(--label-ink);
  }
</style>
</head>
<body>
<main class="label-canvas">
  <svg class="label-shape" width="1200" height="900" viewBox="0 0 1200 900" xmlns="http://www.w3.org/2000/svg">
    <defs>
      <clipPath id="triangle-clip">
        <polygon points="620,178 150,644 1090,644"/>
      </clipPath>
      <linearGradient id="tomato-fill" x1="0" y1="0" x2="1" y2="1">
        <stop offset="0" stop-color="var(--tomato-deep)"/>
        <stop offset="0.5" stop-color="var(--tomato-red)"/>
        <stop offset="1" stop-color="var(--tomato-deep)"/>
      </linearGradient>
      <radialGradient id="basil-fill" cx="0.5" cy="0.5" r="0.5">
        <stop offset="0" stop-color="var(--basil-deep)"/>
        <stop offset="0.7" stop-color="var(--basil-green)"/>
        <stop offset="1" stop-color="var(--basil-green)" stop-opacity="0"/>
      </radialGradient>
    </defs>

    <g class="label-artwork" role="img" aria-label="Painted illustration of sundried tomatoes and basil leaves" clip-path="url(#triangle-clip)">
      <rect x="140" y="170" width="960" height="480" fill="url(#tomato-fill)"/>
      <ellipse cx="650" cy="500" rx="200" ry="210" fill="url(#basil-fill)"/>
      <ellipse cx="230" cy="630" rx="150" ry="90" fill="url(#basil-fill)"/>
    </g>

    <polygon class="label-frame" points="620,174 144,648 1098,648" fill="none" stroke="var(--frame-yellow)" stroke-width="7" stroke-linejoin="miter"/>

    <text class="marinade-name" x="614" y="407" font-size="64" text-anchor="middle">SUNDRIED</text>
    <text class="marinade-name" x="616" y="491" font-size="98" text-anchor="middle">TOMATO</text>
    <text class="marinade-name" x="536" y="540" font-size="40" text-anchor="middle">AND</text>
    <path d="M503 505 q8 -8 20 -4 q20 6 45 -2" fill="none" stroke="var(--label-ink)" stroke-width="4" stroke-linecap="round"/>
    <path d="M503 560 q25 -6 45 -2 q15 3 24 -6" fill="none" stroke="var(--label-ink)" stroke-width="4" stroke-linecap="round"/>
    <text class="marinade-name" x="667" y="556" font-size="94" text-anchor="middle">BASIL</text>

    <text class="ingredients-note" x="621" y="621" text-anchor="middle">PLEASE ASK IN STORE TO SEE SPEC SHEET FOR INGREDIENTS</text>
  </svg>
</main>
</body>
</html>
```